Backup Software Tri-fold Brochure Project

We need a great looking and informative brochure to describe our new Backup Software offering. The brochures are to be used in retail and small business environments given to clients interested in protecting their computer from data loss.
The brochure should include attractive imagery that conveys a sense of Trust and Security to the prospective client.
The copy is provided as an attachment to this project. We'd like our Brisk Harbor product logo to be printed on the back cover. The logo is attached to this project.
The finished tri-fold brochure will be submitted to Loomcraft for printing as an 8.5" x 11" tri-fold brochure. Their design instructions are online http://loomcraft-example.com/custom-brochures.aspx.
The finished product should be Adobe Illustrator CS3 (*.ai) with a PDF Proof.
Target Market(s)
Retail and Small Business customers
Industry/Entity Type
Software
Colors
Designer to choose colors to be used in the design.
Look and feel

```html
<!DOCTYPE html>
<html lang="en">
<head>
<meta charset="utf-8">
<title>Brisk Harbor – Tri-fold Brochure Outer Side</title>
<link rel="stylesheet" href="https://fonts.googleapis.com/css2?family=Exo+2:wght@600;700;800&family=Open+Sans:wght@400;600&display=swap">
<style>
  :root {
    --blue: #1f63b0;
    --blue-deep: #0f3d8c;
    --navy: #0a2a6e;
    --green: #55b332;
    --white: #ffffff;
    --paper: #f7f8fa;
    --ink: #2c3440;
    --bg: #e4e6e9;
  }
  * { box-sizing: border-box; margin: 0; padding: 0; }
  html, body { width: 1200px; height: 1200px; overflow: hidden; background: var(--bg); }
  .brochure {
    position: absolute; left: 40px; top: 167px;
    width: 1120px; height: 866px;
    background: var(--paper);
    box-shadow: 0 10px 30px rgba(0,0,0,.18);
    overflow: hidden;
    font-family: "Open Sans", sans-serif;
  }
  .shapes { position: absolute; inset: 0; }
  .fold { position: absolute; top: 0; bottom: 0; width: 1px; background: rgba(0,0,0,.06); }
  .fold--one { left: 373px; }
  .fold--two { left: 747px; }

  .headline {
    position: absolute; left: 178px; top: 26px; width: 190px;
    font-family: "Exo 2", sans-serif; font-weight: 800; line-height: 1.05;
  }
  .headline__lead { display: block; color: var(--blue-deep); font-size: 34px; }
  .headline__mid { display: block; color: var(--green); font-size: 24px; }
  .headline__tail { display: block; color: var(--blue-deep); font-size: 20px; }

  .facts { position: absolute; left: 30px; top: 612px; width: 320px; color: var(--ink); }
  .facts__title { font-family: "Exo 2", sans-serif; font-weight: 800; color: var(--green); font-size: 27px; }
  .facts__sub { font-family: "Exo 2", sans-serif; font-weight: 700; color: var(--blue-deep); font-size: 17px; margin-bottom: 6px; }
  .facts__list { list-style: none; font-size: 11.5px; line-height: 1.5; }
  .facts__list li::before { content: "\2731"; color: var(--green); margin-right: 7px; font-size: 10px; }
  .sources { margin-top: 8px; padding-left: 18px; font-size: 10px; line-height: 1.4; color: var(--ink); word-break: break-all; }
  .sources li { margin-bottom: 3px; }
  .sources li::marker { color: var(--green); }

  .brand {
    position: absolute; display: flex; align-items: center; gap: 10px;
    font-family: "Exo 2", sans-serif; font-weight: 800; color: var(--blue-deep);
    text-transform: uppercase; letter-spacing: .5px;
  }
  .brand__square { width: 26px; height: 26px; background: var(--green); }
  .brand--back { left: 440px; top: 368px; font-size: 32px; }
  .brand--cover { left: 812px; top: 52px; font-size: 28px; }

  .copyright {
    position: absolute; left: 618px; top: 788px; width: 122px;
    color: var(--white); font-size: 10.5px; line-height: 1.45; text-align: center;
    white-space: nowrap;
  }

  .cover-line {
    position: absolute; left: 830px; top: 630px; color: var(--white);
    font-family: "Exo 2", sans-serif; font-weight: 700;
  }
  .cover-line__small { display: block; font-size: 20px; }
  .cover-line__big { display: block; font-size: 46px; font-weight: 800; line-height: 1; }
</style>
</head>
<body>
<div class="brochure">
  <svg class="shapes" width="1120" height="866" viewBox="0 0 1120 866">
    <defs>
      <radialGradient id="vault-glow" cx="50%" cy="50%" r="50%">
        <stop offset="0" stop-color="#3fb4ea"/>
        <stop offset=".55" stop-color="#1652b5"/>
        <stop offset="1" stop-color="#0a2a6e"/>
      </radialGradient>
      <linearGradient id="cover-art" x1="0" y1="0" x2="1" y2="1">
        <stop offset="0" stop-color="#6aa8e0"/>
        <stop offset=".6" stop-color="#2f78c4"/>
        <stop offset="1" stop-color="#66bf3c"/>
      </linearGradient>
      <clipPath id="left-panel"><rect x="0" y="0" width="373" height="866"/></clipPath>
    </defs>

    <g clip-path="url(#left-panel)">
      <path d="M0 600 C120 560 260 520 373 470 L373 490 C260 545 120 590 0 628 Z" fill="var(--blue)"/>
      <path d="M0 628 C120 590 260 545 373 490" fill="none" stroke="var(--green)" stroke-width="5"/>
      <circle cx="110" cy="330" r="222" fill="url(#vault-glow)" role="img" aria-label="Glowing digital vault with file folders fanning out around it"/>
    </g>

    <path d="M560 866 C640 700 700 560 760 430 C800 340 880 290 1120 210 L1120 866 Z" fill="var(--blue)"/>
    <path d="M545 866 C625 700 685 560 745 430 C785 340 865 290 1120 200" fill="none" stroke="var(--green)" stroke-width="5"/>
    <path d="M530 866 C610 700 670 560 730 430 C770 340 850 285 1120 190" fill="none" stroke="var(--blue)" stroke-width="2"/>
    <path d="M747 560 C850 540 1000 500 1120 440 L1120 452 C1000 515 850 555 747 575 Z" fill="var(--green)"/>

    <rect x="830" y="250" width="240" height="240" rx="16" fill="url(#cover-art)" role="img" aria-label="Laptop and server stack linked by circular sync arrows"/>
  </svg>

  <div class="fold fold--one"></div>
  <div class="fold fold--two"></div>

  <h2 class="headline">
    <span class="headline__lead">The only</span>
    <span class="headline__mid">protection is</span>
    <span class="headline__tail">a great backup</span>
  </h2>

  <section class="facts">
    <h3 class="facts__title">Did You Know?</h3>
    <p class="facts__sub">Every week (in the US)</p>
    <ul class="facts__list">
      <li>140,000 drives crash (1)</li>
      <li>12,000 laptops are lost or stolen (2)</li>
      <li>37,000 Internet Crimes are committed (3)</li>
      <li>Internet criminals steal $25 Million (3)</li>
    </ul>
    <ol class="sources">
      <li>http://www.norrin-example.com/downloads/global/services/norrin_lost_laptop_study.pdf</li>
      <li>http://research.quarrel-example.com/archive/disk_failures.pdf</li>
      <li>https://www.ncrc-example.org/media/annualreport/2016_NCRCReport.pdf</li>
    </ol>
  </section>

  <div class="brand brand--back"><span class="brand__square"></span>Brisk Harbor</div>
  <p class="copyright">Copyright(c) 2017,<br>Tidewell-Net, Inc.<br>All Rights Reserved</p>

  <div class="brand brand--cover"><span class="brand__square"></span>Brisk Harbor</div>
  <p class="cover-line">
    <span class="cover-line__small">Your entire digital Life</span>
    <span class="cover-line__big">IS AT RISK</span>
  </p>
</div>
</body>
</html>
```